New Business Card Design Project

We require a business card design for Vexalund, a newly established Indian company.
Our focus is on the development, manufacturing, and export of a diverse array of pharmaceutical products on a global scale. The card should convey a professional appearance, as our primary markets are in Africa, China, and Southeast Asian nations.
We envision a two-sided business card, with the reverse side dedicated to a logo set against a solid color or an elegantly designed pattern. The corners should be rounded. We would appreciate seeing both horizontal and vertical design options. We trust the designer to utilize their expertise in creating this design.

The content for the business card is included in the attached Word file.

Target Market(s)

Our primary markets are in Africa, China, and Southeast Asian, Latin America, Maldives, Sri Lanka

Industry/Entity Type

Pharmaceutical Manufacturing and Export

Contact Information for Business Card

Colors

Designer to choose colors to be used in the design.

Requirements
Must have
• The reverse side of the business card features solely the logo along with the tagline, "Care Beyond Cure."
Should not have
• The logo should not exceed two instances, encompassing both the front and back sides of the card.

```html
<!DOCTYPE html>
<html lang="en">
<head>
<meta charset="utf-8">
<title>Vexalund – Business Card</title>
<link rel="stylesheet" href="https://fonts.googleapis.com/css2?family=Open+Sans:wght@400;600;700;800&display=swap">
<style>
  :root {
    --backdrop: #232323;
    --card: #1f1f21;
    --brand-blue: #2ea6df;
    --brand-red: #ef5f4c;
    --ink-light: #e8e8e8;
  }
  * { box-sizing: border-box; margin: 0; padding: 0; }
  html, body {
    width: 1200px;
    height: 780px;
    overflow: hidden;
    background: var(--backdrop);
    font-family: "Open Sans", sans-serif;
  }
  .sheet {
    width: 1200px;
    height: 780px;
    display: flex;
    align-items: center;
    justify-content: center;
    gap: 40px;
  }
  .card {
    position: relative;
    width: 540px;
    height: 309px;
    background: var(--card);
    border-radius: 22px;
    box-shadow: 0 10px 30px rgba(0,0,0,0.45);
  }

  /* Front side */
  .holder {
    position: absolute;
    left: 34px;
    top: 32px;
    padding-left: 14px;
    border-left: 5px solid var(--brand-blue);
  }
  .holder-name {
    font-size: 21px;
    line-height: 1.1;
    color: var(--brand-red);
    font-weight: 400;
  }
  .holder-name .first { color: var(--brand-blue); font-weight: 700; }
  .holder-role {
    font-size: 11px;
    color: var(--ink-light);
    letter-spacing: 0.5px;
    margin-top: 2px;
  }
  .address {
    position: absolute;
    left: 53px;
    top: 100px;
    font-size: 11px;
    line-height: 1.5;
    color: var(--brand-blue);
  }
  .contact-list {
    position: absolute;
    left: 38px;
    top: 146px;
    list-style: none;
  }
  .contact-item {
    display: flex;
    align-items: center;
    gap: 7px;
    font-size: 11.5px;
    line-height: 1.75;
    color: var(--ink-light);
  }
  .contact-icon { width: 11px; height: 11px; flex: none; }

  .brand {
    display: flex;
    align-items: center;
    gap: 10px;
    color: var(--brand-blue);
    font-weight: 800;
    letter-spacing: 0.5px;
  }
  .brand-dot { border-radius: 50%; background: var(--brand-red); flex: none; }
  .front .brand {
    position: absolute;
    right: 36px;
    bottom: 40px;
    font-size: 46px;
  }
  .front .brand-dot { width: 22px; height: 22px; }

  /* Back side */
  .back {
    display: flex;
    flex-direction: column;
    align-items: center;
    justify-content: center;
  }
  .back .brand { font-size: 44px; }
  .back .brand-dot { width: 20px; height: 20px; }
  .tagline {
    margin-top: 10px;
    font-size: 13px;
    color: var(--ink-light);
    letter-spacing: 0.5px;
  }
</style>
</head>
<body>
<main class="sheet">
  <section class="card front" aria-label="Card front">
    <div class="holder">
      <p class="holder-name"><span class="first">Arjun</span> K. Tavde</p>
      <p class="holder-role">CEO</p>
    </div>
    <p class="address">12, Nilkamal Nagar,<br>Wardha, 442001, India</p>
    <ul class="contact-list">
      <li class="contact-item">
        <svg class="contact-icon" viewBox="0 0 12 12" aria-hidden="true"><rect x="3" y="0.5" width="6" height="11" rx="1" fill="none" stroke="#ef5f4c" stroke-width="1.2"/></svg>
        +91 98230 41576
      </li>
      <li class="contact-item">
        <svg class="contact-icon" viewBox="0 0 12 12" aria-hidden="true"><circle cx="6" cy="6" r="5" fill="none" stroke="#2ea6df" stroke-width="1.2"/><ellipse cx="6" cy="6" rx="2" ry="5" fill="none" stroke="#2ea6df" stroke-width="1"/><line x1="1" y1="6" x2="11" y2="6" stroke="#2ea6df" stroke-width="1"/></svg>
        www.vexalund.com
      </li>
      <li class="contact-item">
        <svg class="contact-icon" viewBox="0 0 12 12" aria-hidden="true"><rect x="0.6" y="2" width="10.8" height="8" rx="1" fill="none" stroke="#ef5f4c" stroke-width="1.2"/><polyline points="1,3 6,7 11,3" fill="none" stroke="#ef5f4c" stroke-width="1.2"/></svg>
        atavde@vexalund.com
      </li>
    </ul>
    <div class="brand"><span>Vexalund</span><span class="brand-dot"></span></div>
  </section>

  <section class="card back" aria-label="Card back">
    <div class="brand"><span>Vexalund</span><span class="brand-dot"></span></div>
    <p class="tagline">Care Beyond Cure.</p>
  </section>
</main>
</body>
</html>
```